Prospekt für Exklusive Busreisen zu besonderen Zielen!
Zielgruppe
Unser Prospekt soll, ansprechend und Jung sein aber nicht abstoßend dem älteren Publikum gegenüber. Modern und Spritzig. Es soll Ruhe ausstrahlen aber auch für Familien mit Kindern ein Erlebnis werden.
einmalig... besonders... sorgenfrei...Urlaub von Anfang an ohne Kompromisse…
Ich bin gespannt auf die tollen Entwürfe.
Anbei unser Logo und Busbilder. Weitere Bilder oder Reisebilder benutzen Sie bitte irgendwelche Bilder als Platzhalter.
Mit uns erleben Sie die schönsten Theater und Spielorte Europas, wie Sie sie noch nie erlebt haben!
Unsere exklusiven Bus-Touren richten sich an Menschen mit hohen Erwartungen, die es gewohnt sind auf Ihren Reisen auf nichts zu verzichten. Mit unseren 5 Sterne-Bussen bieten wir Ihnen einen der höchsten Standards der Reisebusbranche. Natürlich werden alle Reisen von einer Servicekraft begleitet, die nicht nur Ihr Ansprechpartner während der Fahrt ist, sondern sich auch mit einem Getränke- und Snack-Service um Ihr Wohl kümmert und sich im hinteren Bereich in der Kids Lounge um die kleineren Gäste kümmert. Spielen, Basteln .. für alles ist gesorgt. Ein bequemer Sitzabstand von 81cm lässt Ihnen viel Bewegungsfreiheit. Mit der verstellbaren Fußstütze können sie sich zurücklehnen und entspannen! Der Stromanschluss zum laden Ihres Smartphones oder Tablets ist natürlich Standard. Darüber hinaus sind unsere Busse mit kostenfreien WiFi-Hotspots ausgerüstet. Sie können also noch während Ihrer Reise Bilder an Ihre Freunde und Verwandte senden, Ihre Emails lesen oder z.B. Ihre Lieblingsmusik streamen.
Auch bei den Hotels machen wir keine Abstriche. Auf allen Mehrtagestouren, die Sie bei uns buchen, werden Sie in mindestens 4 Sterne-Hotels untergebracht. Bei der Auswahl der Unterkünfte achten wir natürlich darauf, dass diese der Reise angepasst sind. D.h. bei z.B. Städtereisen möglichst zentrumsnah und bei Konzertre..
Aufgabenstellung
32 Seiten, A4 Quadrat,
Datenformat (inkl. 2,00 mm Beschnitt): 21,40 x 21,40 cm
Endformat (offen): 42,00 x 21,00 cm
Endformat (geschlossen): 21,00 x 21,00 cm

```html
<!DOCTYPE html>
<html lang="de">
<head>
<meta charset="utf-8">
<title>Karl Wendt – Exklusive Busreisen</title>
<link href="https://fonts.googleapis.com/css2?family=Roboto:ital,wght@0,400;0,500;0,700;0,900;1,400&display=swap" rel="stylesheet">
<style>
:root{
  --navy:#0b2676;
  --navy-dark:#07195a;
  --orange:#f2703a;
  --ink:#1d1d1d;
  --white:#ffffff;
  --panel:rgba(255,255,255,.9);
  --page-bg:#ffffff;
}
*{box-sizing:border-box;margin:0;padding:0}
html,body{width:1200px;height:2301px;overflow:hidden;background:var(--page-bg)}
body{position:relative;font-family:'Roboto',Arial,sans-serif;color:var(--ink)}
.sheet{position:absolute;overflow:hidden}
.photo{position:absolute}
.abs{position:absolute}

/* cover */
.cover{left:93px;top:77px;width:505px;height:506px;background:linear-gradient(180deg,#e6ebe6 0%,#c9a27a 40%,#7a4e35 65%,#3b2b2a 80%)}
.cover-wave{position:absolute;left:0;top:300px;width:505px;height:206px}
.brand-name{position:absolute;left:33px;top:356px;color:var(--white);font-size:7.5px;font-weight:700;letter-spacing:2px}
.brand-mark{position:absolute;left:36px;top:377px;width:32px;height:32px;border-radius:50%;background:var(--white)}
.contact{position:absolute;left:33px;top:437px;color:var(--white)}
.contact .phone{font-size:16px;font-weight:500}
.contact .mail{font-size:10px;margin-top:1px}
.contact .addr{font-size:8px;margin-top:6px;letter-spacing:.3px}
.slogan{position:absolute;right:32px;top:410px;text-align:right;color:var(--orange);font-size:16.5px;font-weight:700;line-height:18.5px}
.slogan .tag{display:block;color:var(--white);font-size:8.5px;font-weight:500;line-height:12px;margin-top:6px;letter-spacing:.3px}

/* welcome spread */
.welcome{left:93px;top:623px;width:1010px;height:506px;background:radial-gradient(ellipse at 62% 30%,#d9a067 0%,#6d4530 18%,#1a1616 45%,#0c0c0e 100%)}
.welcome h1{position:absolute;left:32px;top:188px;color:var(--white);font-size:30px;line-height:31px;font-weight:700}
.welcome .lead{position:absolute;left:32px;top:259px;width:430px;color:var(--white);font-size:12.6px;line-height:16px}
.welcome .col{position:absolute;top:347px;width:212px;color:var(--white);font-size:7.2px;line-height:10.2px}
.welcome .side{position:absolute;left:541px;top:149px;width:145px;color:var(--white);font-size:7px;line-height:10.2px}
.welcome .side-lead{position:absolute;left:541px;top:273px;width:150px;color:var(--white);font-size:13.5px;line-height:16px}
.features{position:absolute;left:541px;top:352px;list-style:none;color:var(--white);font-size:8px;font-style:italic;line-height:13.2px}
.features li::before{content:"•";margin-right:5px}
.framed{position:absolute;border:3px solid var(--white)}
.folio{position:absolute;top:482px;font-size:6.5px}
.welcome .folio{color:var(--white)}

/* destination grid */
.tile{position:absolute;overflow:hidden}
.tile-label{position:absolute;left:32px;top:18px;font-size:11px;font-weight:700;letter-spacing:.4px;color:var(--white)}
.tile-label.dark{color:var(--ink)}
.offer{position:absolute;background:var(--panel);padding:8px 8px 0 8px;font-size:7px;line-height:9.5px}
.offer h3{font-size:12px;font-weight:700;padding-bottom:2px;border-bottom:1px solid var(--navy);margin-bottom:5px}
.offer .label{color:var(--orange)}
.offer .dates b{font-weight:700}
.offer .incl{color:var(--navy);font-style:italic;font-size:6.4px;line-height:9px;margin:5px 0 8px}
.offer .price{display:flex;justify-content:space-between;align-items:baseline}
.offer .price span:last-child{font-size:11px;font-weight:700}
.offer .early span:last-child{color:var(--orange)}
.offer .regular span:last-child{color:var(--navy)}

/* detail spread */
.detail{left:90px;top:1728px;width:1012px;height:506px;background:var(--white);border:1px solid #d9d9d9}
.detail .map{left:0;top:0;width:205px;height:82px;background:linear-gradient(180deg,#dde8f4,#f3f7fb)}
.detail .left{position:absolute;left:33px;top:84px;width:150px;font-size:7.3px;line-height:10.2px}
.detail .left .label{color:var(--orange)}
.detail .left p{margin-top:10px}
.detail .left .extras{color:var(--navy);font-style:italic}
.detail .left .extras b{font-style:normal}
.city{position:absolute;left:32px;top:308px;font-size:33px;font-weight:900;color:var(--ink)}
.departure{position:absolute;left:0;top:357px;width:205px;height:40px;background:var(--navy);color:var(--white);font-size:6.8px;font-weight:500;line-height:9.5px;padding:11px 0 0 33px}
.price-box{position:absolute;left:205px;top:357px;width:91px;height:40px;background:var(--navy);color:var(--white);font-size:23px;font-weight:500;padding:5px 0 0 19px}
.price-early{position:absolute;left:226px;top:410px;color:var(--white);font-size:7px;line-height:10px;text-align:center}
.price-early b{display:block;font-size:12px;font-weight:500}
.footnote{position:absolute;left:33px;top:413px;width:150px;color:var(--navy);font-style:italic;font-size:7px;line-height:9.5px}
.program{position:absolute;left:540px;top:84px;width:232px;font-size:7px;line-height:10px}
.program ol{list-style:none}
.program li{margin-top:6px;padding-left:9px;text-indent:-9px}
</style>
</head>
<body>

<!-- Cover -->
<section class="sheet cover">
  <div class="photo" style="left:0;top:0;width:505px;height:360px;background:linear-gradient(180deg,#e8ece7 0%,#cfa57a 45%,#8a5a3c 70%,#e4b9c6 100%)" role="img" aria-label="Altstadtgasse mit Fachwerkhäusern, Torturm und Blumen"></div>
  <svg class="cover-wave" viewBox="0 0 505 206" preserveAspectRatio="none" aria-hidden="true">
    <path d="M0 32 C120 -10 230 40 330 36 C420 32 470 10 505 4 L505 206 L0 206 Z" fill="#1d47a8" opacity=".55"/>
    <path d="M0 42 C120 5 230 55 330 50 C420 46 470 22 505 18 L505 206 L0 206 Z" fill="var(--navy)"/>
  </svg>
  <div class="brand-name">KARL WENDT</div>
  <div class="brand-mark" aria-hidden="true"></div>
  <div class="contact">
    <div class="phone">+179 987 65 43</div>
    <div class="mail">reisen@wendtbus.de</div>
    <div class="addr">Lindenweg 4 · 75010 Beispielstadt</div>
  </div>
  <div class="slogan">...EINMALIG<br>...BESONDERS<br>...SORGENFREI<span class="tag">Urlaub von Anfang an ohne Kompromisse.</span></div>
</section>

<!-- Welcome spread -->
<section class="sheet welcome">
  <div class="photo" style="inset:0;background:radial-gradient(ellipse at 62% 28%,rgba(240,180,110,.75) 0%,rgba(110,70,45,.5) 20%,rgba(0,0,0,0) 50%)" role="img" aria-label="Fahrgäste im Reisebus im Gegenlicht"></div>
  <h1>HERZLICH WILLKOMMEN<br>BEI KARL WENDT!</h1>
  <p class="lead">Lorem Ipsum ist ein einfacher Demo-Text für die Print- und Schriftindustrie. Lorem Ipsum ist in der Industrie bereits der Standard Demo-Text seit 1500, als ein unbekannter Schriftsteller eine Hand voll Wörter nahm und diese durcheinander warf um ein</p>
  <p class="col" style="left:32px">Lorem Ipsum ist ein einfacher Demo-Text für die Print- und Schriftindustrie. Lorem Ipsum ist in der Industrie bereits der Standard Demo-Text seit 1500, als ein unbekannter Schriftsteller eine Hand voll Wörter nahm und diese durcheinander warf um ein Musterbuch zu erstellen. Es hat nicht nur 5 Jahrhunderte überlebt, sondern auch in Spruch in die elektronische Schriftbearbeitung geschafft (bemerke, nahezu unverändert). Bekannt wurde es 1960, mit dem</p>
  <p class="col" style="left:264px">Lorem Ipsum ist ein einfacher Demo-Text für die Print- und Schriftindustrie. Lorem Ipsum ist in der Industrie bereits der Standard Demo-Text seit 1500, als ein unbekannter Schriftsteller eine Hand voll Wörter nahm und diese durcheinander warf um ein Musterbuch zu erstellen. Es hat nicht nur 5 Jahrhunderte überlebt, sondern auch in Spruch in die elektronische Schriftbearbeitung geschafft (bemerke, nahezu unverändert). Bekannt wurde es 1960, mit dem</p>
  <p class="side">Lorem Ipsum ist ein einfacher Demo-Text für die Print- und Schriftindustrie. Lorem Ipsum ist in der Industrie bereits der Standard Demo-Text seit 1500, als ein unbekannter Schriftsteller eine Hand voll Wörter nahm und diese durcheinander warf um ein Musterbuch zu erstellen. Es hat nicht nur 5 Jahrhunderte überlebt, sondern auch in Spruch in die elektronische Schriftbearbeitung geschafft (bemerke, nahezu</p>
  <p class="side-lead">Lorem Ipsum ist ein einfacher Demo-Text für die Print- und Schriftindustrie. Lorem</p>
  <ul class="features">
    <li>5 Sterne-Bussen</li>
    <li>Getränke- und Snack-Service</li>
    <li>Kids Lounge Service</li>
    <li>Sitzabstand von 81cm</li>
    <li>Verstellbaren Fußstütze</li>
    <li>Kostenfreie WiFi-Hotspot</li>
  </ul>
  <div class="framed" style="left:784px;top:29px;width:207px;height:143px;background:linear-gradient(180deg,#8fc3c6,#b7926c 60%,#5a3e2e)" role="img" aria-label="Innenraum des Reisebusses mit Ledersitzen"></div>
  <div class="framed" style="left:876px;top:194px;width:123px;height:163px;background:linear-gradient(180deg,#b8d8e0,#7a5a46 55%,#3b2c25)" role="img" aria-label="Mittelgang im Reisebus"></div>
  <div class="framed" style="left:710px;top:343px;width:240px;height:143px;background:linear-gradient(180deg,#e8eaee,#c7ccd6 55%,#9aa1ad)" role="img" aria-label="Büro mit Schreibtisch und Bildschirmen"></div>
  <span class="folio" style="left:32px">2</span>
  <span class="folio" style="left:975px">3</span>
</section>

<!-- Destination overview spread -->
<section class="sheet" style="left:90px;top:1181px;width:1016px;height:505px">

  <div class="tile" style="left:0;top:0;width:253px;height:281px;background:linear-gradient(160deg,#8a7460,#4a3d33 55%,#8e1c1c)" role="img" aria-label="Fassade mit Rundbogenfenster und roter Telefonzelle">
    <div class="tile-label">MEHRTAGESREISEN</div>
    <div class="offer" style="left:4px;top:143px;width:132px;height:134px">
      <h3>Dresden</h3><div class="label">Termine:</div>
      <div class="dates"><b>09.04.-13.04.2020</b> (Ostern)<br><b>26.08.-30.08.2020</b> (Sommer)</div>
      <div class="incl">1 Übernachtung mit Früh- stücksbuffet im guten 3***-Hotel Lindenhof Styles Dresden Neustadt, Reiseleitung</div>
      <div class="price early"><span>Frühbucherpreis</span><span>€188</span></div>
      <div class="price regular"><span>Normalpreis</span><span>€208</span></div>
    </div>
  </div>

  <div class="tile" style="left:0;top:288px;width:253px;height:217px;background:linear-gradient(180deg,#e9e4df,#c98b62 55%,#2f7f86)" role="img" aria-label="Luftbild einer Lagunenstadt mit Kuppelkirche">
    <div class="offer" style="left:117px;top:4px;width:135px;height:135px">
      <h3>Milano</h3><div class="label">Termine:</div>
      <div class="dates"><b>09.04.-13.04.2020</b> (Ostern)<br><b>26.08.-30.08.2020</b> (Sommer)</div>
      <div class="incl">1 Übernachtung mit Früh- stücksbuffet im guten 3***-Hotel Lindenhof Styles Dresden Neustadt, Reiseleitung</div>
      <div class="price early"><span>Frühbucherpreis</span><span>€188</span></div>
      <div class="price regular"><span>Normalpreis</span><span>€208</span></div>
    </div>
  </div>

  <div class="tile" style="left:260px;top:0;width:245px;height:238px;background:linear-gradient(120deg,#c9a27c,#e8dccb 45%,#3d5fa8 80%,#c96b3a)" role="img" aria-label="Enge Gasse mit bunten Häusern und Blumen">
    <div class="tile-label">TAGESTOUREN</div>
    <div class="offer" style="left:1px;top:98px;width:135px;height:135px">
      <h3>Milano</h3><div class="label">Termine:</div>
      <div class="dates"><b>09.04.-13.04.2020</b> (Ostern)<br><b>26.08.-30.08.2020</b> (Sommer)</div>
      <div class="incl">1 Übernachtung mit Früh- stücksbuffet im guten 3***-Hotel Lindenhof Styles Dresden Neustadt, Reiseleitung</div>
      <div class="price early"><span>Frühbucherpreis</span><span>€188</span></div>
      <div class="price regular"><span>Normalpreis</span><span>€208</span></div>
    </div>
  </div>

  <div class="tile" style="left:260px;top:246px;width:245px;height:259px;background:linear-gradient(180deg,#9a9890,#c7b46a 45%,#5b564c)" role="img" aria-label="Straßenszene mit vorbeifahrender gelber Straßenbahn">
    <div class="offer" style="left:111px;top:121px;width:134px;height:135px">
      <h3>Amsterdam</h3><div class="label">Termine:</div>
      <div class="dates"><b>09.04.-13.04.2020</b> (Ostern)<br><b>26.08.-30.08.2020</b> (Sommer)</div>
      <div class="incl">1 Übernachtung mit Früh- stücksbuffet im guten 3***-Hotel Lindenhof Styles Dresden Neustadt, Reiseleitung</div>
      <div class="price early"><span>Frühbucherpreis</span><span>€188</span></div>
      <div class="price regular"><span>Normalpreis</span><span>€208</span></div>
    </div>
  </div>

  <div class="tile" style="left:512px;top:0;width:246px;height:238px;background:linear-gradient(180deg,#eee4dc,#d2b9a3 50%,#6d6a62)" role="img" aria-label="Stadtansicht mit großer Kuppelkirche am Fluss">
    <div class="tile-label dark">MESSE REISEN</div>
    <div class="offer" style="left:32px;top:100px;width:135px;height:135px">
      <h3>Rom</h3><div class="label">Termine:</div>
      <div class="dates"><b>09.04.-13.04.2020</b> (Ostern)<br><b>26.08.-30.08.2020</b> (Sommer)</div>
      <div class="incl">1 Übernachtung mit Früh- stücksbuffet im guten 3***-Hotel Lindenhof Styles Dresden Neustadt, Reiseleitung</div>
      <div class="price early"><span>Frühbucherpreis</span><span>€188</span></div>
      <div class="price regular"><span>Normalpreis</span><span>€208</span></div>
    </div>
  </div>

  <div class="tile" style="left:512px;top:246px;width:246px;height:259px;background:linear-gradient(180deg,#7c8590,#5a4a40 55%,#3a2f2a)" role="img" aria-label="Burg im Wald mit Kopfsteinpflasterweg">
    <div class="offer" style="left:109px;top:1px;width:136px;height:135px">
      <h3>Dresden</h3><div class="label">Termine:</div>
      <div class="dates"><b>09.04.-13.04.2020</b> (Ostern)<br><b>26.08.-30.08.2020</b> (Sommer)</div>
      <div class="incl">1 Übernachtung mit Früh- stücksbuffet im guten 3***-Hotel Lindenhof Styles Dresden Neustadt, Reiseleitung</div>
      <div class="price early"><span>Frühbucherpreis</span><span>€188</span></div>
      <div class="price regular"><span>Normalpreis</span><span>€208</span></div>
    </div>
  </div>

  <div class="tile" style="left:764px;top:0;width:252px;height:281px;background:linear-gradient(180deg,#6f7479,#4b4540 50%,#2a2522)" role="img" aria-label="Barocke Kirchenkuppel unter bewölktem Himmel">
    <div class="tile-label">MESSE REISEN</div>
    <div class="offer" style="left:60px;top:143px;width:134px;height:135px">
      <h3>Dresden</h3><div class="label">Termine:</div>
      <div class="dates"><b>09.04.-13.04.2020</b> (Ostern)<br><b>26.08.-30.08.2020</b> (Sommer)</div>
      <div class="incl">1 Übernachtung mit Früh- stücksbuffet im guten 3***-Hotel Lindenhof Styles Dresden Neustadt, Reiseleitung</div>
      <div class="price early"><span>Frühbucherpreis</span><span>€188</span></div>
      <div class="price regular"><span>Normalpreis</span><span>€208</span></div>
    </div>
  </div>

  <div class="tile" style="left:764px;top:288px;width:252px;height:217px;background:linear-gradient(180deg,#4f8fa8,#c9b8a0 45%,#8a7a68 80%,#9ab7b3)" role="img" aria-label="Barocker Brunnen vor einem Palast">
    <div class="offer" style="left:0;top:2px;width:135px;height:137px">
      <h3>Rom</h3><div class="label">Termine:</div>
      <div class="dates"><b>09.04.-13.04.2020</b> (Ostern)<br><b>26.08.-30.08.2020</b> (Sommer)</div>
      <div class="incl">1 Übernachtung mit Früh- stücksbuffet im guten 3***-Hotel Lindenhof Styles Dresden Neustadt, Reiseleitung</div>
      <div class="price early"><span>Frühbucherpreis</span><span>€188</span></div>
      <div class="price regular"><span>Normalpreis</span><span>€208</span></div>
    </div>
  </div>
</section>

<!-- Detail spread -->
<section class="sheet detail">
  <div class="photo map" role="img" aria-label="Europakarte mit Markierung des Reiseziels"></div>
  <svg class="abs" style="left:168px;top:43px" width="11" height="15" viewBox="0 0 11 15" aria-hidden="true">
    <path d="M5.5 0.8C2.9 0.8 1 2.8 1 5.2c0 3.3 4.5 8.9 4.5 8.9S10 8.5 10 5.2C10 2.8 8.1 0.8 5.5 0.8z" fill="none" stroke="var(--orange)" stroke-width="1.4"/>
    <circle cx="5.5" cy="5.2" r="1.6" fill="var(--orange)"/>
  </svg>
  <div class="left">
    <div class="label">Termine:</div>
    <div><b>09.04.-13.04.2020</b> (Ostern)<br><b>26.08.-30.08.2020</b> (Sommer)<br><b>28.09.-30.09.2020</b> (Herbst)<br><b>15.11.-18.11.2020</b></div>
    <p>Reich an Kunst und Kultur zeigt sich Sachsens Landeshauptstadt vor barocker Kulisse. Voller Le- bensfreude genießen die Dresdener ihre Stadt auf Straßen und Plätzen, auf Bühnen mit Künstlern von Weltrang und laden Gäste aus aller Welt ein, es ihnen gleich zu tun. Auch die Zahl der Sehenswür- digkeiten ist groß. Die Frauenkirche, das Schloß, die Semperoper, das grüne Gewölbe und viele weitere Attraktionen warten darauf, von Ihnen entdeckt zu werden.</p>
    <p class="extras"><b>Leistungen:</b> Busreise, 1 Übernachtung mit Früh- stücksbuffet im guten 4****-Hotel Lindenhof Styles Dresden Neustadt, Reiseleitung</p>
  </div>
  <div class="city">DRESDEN</div>
  <div class="photo" style="left:205px;top:0;width:301px;height:506px;background:linear-gradient(180deg,#3c3e42,#6b5a48 40%,#8a6b4c 60%,#3a302a)" role="img" aria-label="Barocke Kirchenkuppel mit Turm vor dunklem Himmel"></div>
  <div class="departure">Abfahrt: 05.00 Uhr Musterstadt, Musterplatz<br>Zusätzliches Angebot: Lichterrundfahrt (18,–)</div>
  <div class="price-box">€208</div>
  <div class="price-early">Frühbucherpreis<b>€188</b></div>
  <p class="footnote">Frühbucherpreis Preis pro Person gültig für Buchungen bis 6 Wochen vor Reisebeginn.</p>
  <span class="folio" style="left:33px;top:478px">6</span>

  <div class="program">
    <b>Programm:</b>
    <ol>
      <li><b>1.Tag</b> Abfahrt <b>7.00</b> Uhr Augsburg, Plärrer <b>8.00</b> Uhr München, Busterminal Fröttmaning nachmittags Stadtführung (€ 18,–) und freie Zeit in Vicenza, Transfer ins Hotel</li>
      <li><b>2. Tag</b> Stadtführung in Padua (€ 18,–), nachmittags Zeit zur freien Verfügung</li>
      <li><b>3. Tag</b> Ausflug nach Verona, dort Stadtführung (€ 18,–), danach Rückreise, Ankunft in Deutschland am späten Abend</li>
    </ol>
  </div>
  <div class="photo" style="left:506px;top:195px;width:506px;height:311px;background:radial-gradient(ellipse at 45% 55%,#6a5a4a 0%,#3a3430 45%,#1f1c1b 100%)" role="img" aria-label="Besucher betrachtet große Gemälde in einem Museum"></div>
  <div class="framed" style="left:795px;top:-3px;width:216px;height:315px;background:linear-gradient(180deg,#e8e6e2,#cfc7b8 45%,#b8995c 70%,#8e8270)" role="img" aria-label="Kirchenkuppel mit Orgel und goldenen Verzierungen"></div>
  <span class="folio" style="left:975px;top:478px">7</span>
</section>

</body>
</html>
```